Professional and Fun Business Cards for #1 Lagoon Care

We want an updated look for our existing business cards. In addition, we need to update the logos on the back side of the card to be the most current award for Tovey's Index. I have an eps of the Tovey's Index award logo but it is too big to upload here, so I can email it to the designer once selected.

Target Market(s)

Families with swimming pools

Industry/Entity Type

Business

Contact Information for Business Card

Martin Dobrev
Partner & Senior Pool Technician
Dobrev & Kin Pool Service, Inc.
2480 Larkhaven Drive, Suite 312
Roseville, CA 95874
(916) 555-0143 service
(916) 555-0187 billing
info@dobrev-kin.example
www.dobrev-kin.example

Font styles to use
Other font styles liked:
• Goudy Sans Bold

Colors
3176b5
34a7d8
34b8a4
add136

Requirements
Must have
• Dobrev & Kin logo and contact information on the front
• All other logos on the back
Nice to have
• Open to ideas...
Should not have
• Can't think of anything specific

```html
<!DOCTYPE html>
<html lang="en">
<head>
<meta charset="utf-8">
<title>Dobrev &amp; Kin Pool Service – Business Cards</title>
<link href="https://fonts.googleapis.com/css2?family=Open+Sans:wght@400;600;700&display=swap" rel="stylesheet">
<style>
  :root {
    --page: #e9ecef;
    --card-white: #ffffff;
    --white-edge: #eef1f4;
    --blue-light: #5fbbe3;
    --blue-mid: #3f9fd4;
    --blue-deep: #2c7fbd;
    --brand-blue: #3176b5;
    --name-ink: #1f2a33;
    --text-on-blue: #ffffff;
    --badge-gold: #d9c45a;
    --badge-green: #34b8a4;
    --badge-grey: #c9d3dc;
  }
  * { box-sizing: border-box; margin: 0; padding: 0; }
  html, body { width: 1200px; height: 885px; overflow: hidden; }
  body {
    background: var(--page);
    font-family: "Open Sans", Arial, sans-serif;
    position: relative;
  }
  .card {
    position: absolute;
    width: 640px;
    height: 366px;
    border-radius: 22px;
    overflow: hidden;
    background: var(--card-white);
    box-shadow: 0 10px 30px rgba(20, 40, 60, 0.18);
  }
  .card--front { left: 60px; top: 50px; }
  .card--back { left: 500px; top: 470px; }

  .white-band {
    position: absolute; left: 0; right: 0; top: 0;
    background: linear-gradient(180deg, var(--card-white), var(--white-edge));
  }
  .blue-field {
    position: absolute; left: 0; right: 0; bottom: 0;
    background: linear-gradient(160deg, var(--blue-light) 0%, var(--blue-mid) 55%, var(--blue-deep) 100%);
  }
  .card--front .white-band { height: 150px; }
  .card--front .blue-field { top: 150px; }

  .wordmark {
    position: absolute;
    display: flex; align-items: center; gap: 10px;
    color: var(--brand-blue);
    font-weight: 700;
    white-space: nowrap;
    line-height: 1.2;
  }
  .wordmark__square {
    width: 28px; height: 28px;
    background: var(--brand-blue);
    border-radius: 3px;
  }
  .card--front .wordmark { left: 30px; top: 94px; font-size: 30px; }

  .company-name {
    position: absolute;
    color: var(--blue-mid);
    font-weight: 600;
    font-size: 21px;
    white-space: nowrap;
    line-height: 1.3;
  }
  .card--front .company-name { right: 34px; top: 20px; }

  .person { position: absolute; right: 34px; top: 58px; text-align: right; color: var(--name-ink); }
  .person__name { font-size: 19px; font-weight: 700; line-height: 1.25; }
  .person__title { font-size: 13px; font-weight: 600; line-height: 1.4; }

  .contact {
    position: absolute; right: 26px; top: 168px;
    list-style: none;
    color: var(--text-on-blue);
    font-size: 13.5px; font-weight: 600;
    text-align: right;
    line-height: 22px;
  }
  .contact li { display: flex; justify-content: flex-end; align-items: center; gap: 10px; white-space: nowrap; }
  .contact .icon {
    width: 18px; height: 18px; flex: none;
    border-radius: 4px;
    background: rgba(255, 255, 255, 0.85);
    display: flex; align-items: center; justify-content: center;
  }
  .contact .icon svg { width: 12px; height: 12px; }
  .contact .no-icon { width: 18px; flex: none; }

  .badges { position: absolute; left: 150px; bottom: 24px; display: flex; gap: 18px; }
  .badge {
    width: 64px; height: 56px; border-radius: 8px;
    background: rgba(255, 255, 255, 0.92);
    display: flex; align-items: center; justify-content: center;
  }
  .badge__seal { width: 38px; height: 38px; border-radius: 50%; }
  .badge__seal--award { background: var(--badge-gold); box-shadow: 0 0 0 4px var(--badge-green); }
  .badge__seal--cert { background: var(--badge-grey); box-shadow: 0 0 0 3px var(--brand-blue); }

  .card--back .white-band { height: 228px; }
  .card--back .blue-field { top: 228px; }
  .card--back .wordmark { left: 50%; top: 90px; transform: translateX(-50%); font-size: 40px; }
  .card--back .wordmark__square { width: 36px; height: 36px; }
  .card--back .company-name {
    left: 0; right: 0; top: 276px; text-align: center;
    color: var(--text-on-blue); font-size: 24px;
  }
</style>
</head>
<body>
  <section class="card card--front" aria-label="Business card front">
    <div class="white-band"></div>
    <div class="blue-field"></div>

    <div class="wordmark"><span class="wordmark__square"></span>Dobrev &amp; Kin</div>
    <p class="company-name">Dobrev &amp; Kin Pool Service, Inc</p>
    <div class="person">
      <p class="person__name">Martin Dobrev</p>
      <p class="person__title">Partner &amp; Senior Pool Technician</p>
    </div>

    <ul class="contact">
      <li>(916) 555-0143
        <span class="icon"><svg viewBox="0 0 12 12"><path d="M3 1l2 2-1 1.5a6 6 0 0 0 3.5 3.5L9 7l2 2-1.5 2C5 11 1 7 1 2.5z" fill="#3f9fd4"/></svg></span></li>
      <li>(916) 555-0187
        <span class="icon"><svg viewBox="0 0 12 12"><path d="M3 1l2 2-1 1.5a6 6 0 0 0 3.5 3.5L9 7l2 2-1.5 2C5 11 1 7 1 2.5z" fill="#3f9fd4"/></svg></span></li>
      <li>info@dobrev-kin.example
        <span class="icon"><svg viewBox="0 0 12 12"><rect x="1" y="2.5" width="10" height="7" fill="none" stroke="#3f9fd4" stroke-width="1.3"/><path d="M1 2.5l5 4 5-4" fill="none" stroke="#3f9fd4" stroke-width="1.3"/></svg></span></li>
      <li>www.dobrev-kin.example
        <span class="icon"><svg viewBox="0 0 12 12"><circle cx="6" cy="6" r="4.6" fill="none" stroke="#3f9fd4" stroke-width="1.2"/><path d="M1.4 6h9.2M6 1.4c-2.4 2.6-2.4 6.6 0 9.2M6 1.4c2.4 2.6 2.4 6.6 0 9.2" fill="none" stroke="#3f9fd4" stroke-width="1"/></svg></span></li>
      <li>2480 Larkhaven Drive, Suite 312 Roseville
        <span class="icon"><svg viewBox="0 0 12 12"><path d="M6 11.5S2 7 2 4.5a4 4 0 0 1 8 0C10 7 6 11.5 6 11.5z" fill="#3f9fd4"/><circle cx="6" cy="4.5" r="1.4" fill="#fff"/></svg></span></li>
      <li>CA 95874<span class="no-icon"></span></li>
    </ul>

    <div class="badges">
      <div class="badge"><span class="badge__seal badge__seal--award" role="img" aria-label="Tovey's Index award badge"></span></div>
      <div class="badge"><span class="badge__seal badge__seal--cert" role="img" aria-label="Certified pool operator badge"></span></div>
    </div>
  </section>

  <section class="card card--back" aria-label="Business card back">
    <div class="white-band"></div>
    <div class="blue-field"></div>
    <div class="wordmark"><span class="wordmark__square"></span>Dobrev &amp; Kin</div>
    <p class="company-name">Dobrev &amp; Kin Pool Service, Inc</p>
  </section>
</body>
</html>
```